Cedar Brook Stables, LLC

Equestrian business card to promote equine retirement, farm sitting, short term board. Located in Aiken, SC.
Updates
Updated color schemes.
Contact Information for Business Card
Contact info, description of work.
Colors
0094D4
00A9DD
6FCCEA
C7EBF8
E9F6FB
59FF00
82FF00
B8FF75
E3FFCB
F4FFEA
F0912C
F2A743
F7CA91
FBE8D2
FDF5EE

```html
<!DOCTYPE html>
<html lang="en">
<head>
<meta charset="UTF-8">
<title>Cedar Brook Stables, LLC — Business Card</title>
<link rel="stylesheet" href="https://fonts.googleapis.com/css2?family=Poppins:wght@500;600;700&family=Arimo:wght@400&display=swap">
<style>
  :root {
    --stage: #2b2b2b;
    --card-dark: #111111;
    --card-light: #ffffff;
    --sun-yellow: #f7c51e;
    --accent-orange: #f2a743;
    --farm-green: #0e7a12;
    --ink: #1a1a1a;
    --mark-text: #e6e6e6;
    --rule: #9a9a9a;
  }
  * { box-sizing: border-box; margin: 0; padding: 0; }
  html, body {
    width: 1200px; height: 1040px; overflow: hidden;
    background: var(--stage);
  }
  .card {
    position: absolute;
    left: 270px;
    width: 660px; height: 380px;
    border-radius: 0 70px 0 70px;
    box-shadow: 0 14px 30px rgba(0,0,0,0.55);
  }
  .card--back { top: 110px; background: var(--card-dark); }
  .card--front { top: 550px; background: var(--card-light); }

  .brand {
    position: absolute;
    display: flex; align-items: center; gap: 16px;
  }
  .brand__dot {
    width: 64px; height: 64px; border-radius: 50%;
    background: var(--sun-yellow); flex: none;
  }
  .brand__name {
    font-family: "Poppins", sans-serif; font-weight: 600;
    font-size: 22px; letter-spacing: 2px; line-height: 1.25;
    text-transform: uppercase;
  }
  .card--back .brand { left: 50%; top: 110px; transform: translateX(-50%); }
  .card--back .brand__name { color: var(--mark-text); }
  .card--front .brand { left: 40px; top: 150px; }
  .card--front .brand__name { color: var(--farm-green); font-size: 20px; }

  .services {
    position: absolute; left: 0; right: 0; top: 285px;
    text-align: center;
    font-family: "Poppins", sans-serif; font-weight: 600;
    font-size: 18px; letter-spacing: 0.8px;
    color: var(--sun-yellow);
  }
  .services .sep { margin: 0 12px; }

  .divider {
    position: absolute; left: 345px; top: 80px;
    width: 1px; height: 230px; background: var(--rule);
  }
  .contact {
    position: absolute; left: 370px; top: 78px; width: 280px;
    font-family: "Arimo", sans-serif; color: var(--ink);
  }
  .contact__name {
    font-family: "Poppins", sans-serif; font-weight: 700;
    font-size: 24px; letter-spacing: 1.5px; line-height: 1.1;
    color: var(--farm-green); text-transform: uppercase;
  }
  .contact__role { font-size: 17px; letter-spacing: 0.8px; margin-top: 2px; }
  .contact__list { list-style: none; margin-top: 14px; }
  .contact__item {
    display: flex; align-items: center; gap: 8px;
    font-size: 16px; letter-spacing: 0.4px; margin-bottom: 6px;
  }
  .contact__item svg { width: 16px; height: 16px; flex: none; }
  .contact__web-name { color: var(--farm-green); }
  .contact__address {
    font-style: normal; font-size: 16px; line-height: 1.35;
    letter-spacing: 0.4px; margin-top: 12px;
  }
</style>
</head>
<body>
  <section class="card card--back" aria-label="Card back">
    <div class="brand">
      <span class="brand__dot"></span>
      <span class="brand__name">Cedar Brook Stables, LLC</span>
    </div>
    <p class="services">Short Term Board<span class="sep">|</span>Farm sitting<span class="sep">|</span>Equine Retirement</p>
  </section>

  <section class="card card--front" aria-label="Card front">
    <div class="brand">
      <span class="brand__dot"></span>
      <span class="brand__name">Cedar Brook<br>Stables, LLC</span>
    </div>
    <span class="divider"></span>
    <div class="contact">
      <h1 class="contact__name">Daniel Whitford</h1>
      <p class="contact__role">Managing Director</p>
      <ul class="contact__list">
        <li class="contact__item">
          <svg viewBox="0 0 24 24" aria-hidden="true"><path fill="var(--accent-orange)" d="M6.6 10.8a15 15 0 0 0 6.6 6.6l2.2-2.2c.3-.3.7-.4 1-.2 1.1.4 2.3.6 3.6.6.6 0 1 .4 1 1V20c0 .6-.4 1-1 1A17 17 0 0 1 3 4c0-.6.4-1 1-1h3.5c.6 0 1 .4 1 1 0 1.3.2 2.5.6 3.6.1.3 0 .7-.2 1z"/></svg>
          803-555-0142
        </li>
        <li class="contact__item">
          <svg viewBox="0 0 24 24" aria-hidden="true"><rect x="2" y="5" width="20" height="14" rx="1" fill="var(--accent-orange)"/><path d="M2 6l10 7 10-7" fill="none" stroke="#fff" stroke-width="1.6"/></svg>
          hello@cedarbrookstables.com
        </li>
        <li class="contact__item">
          <svg viewBox="0 0 24 24" aria-hidden="true"><g fill="none" stroke="var(--accent-orange)" stroke-width="1.8"><circle cx="12" cy="12" r="9"/><ellipse cx="12" cy="12" rx="4" ry="9"/><path d="M3 12h18M5 7h14M5 17h14"/></g></svg>
          <span>www.<span class="contact__web-name">cedarbrookstables</span>.com</span>
        </li>
      </ul>
      <address class="contact__address">214 Fox Hollow Lane<br>Aiken, SC 29801</address>
    </div>
  </section>
</body>
</html>
```